NEW Wordpress Website Design for a Dynamic Long Term Healthcare Company in Hawaii

I would like a new website design for my current company, Marlow Health Collective, which has two different brands - Marlow Homecare and Marlow Senior Living. You can see the current website at www.marlowhealth-example.com. The website should be built using Wordpress Software and the Framewise theme. The website should have a local Hawaii island/tropical feel, but look professional for healthcare. I'm looking for something fresh, and want the designer to select colors, styles, etc.

In the Header, on all pages, I would like a menu that includes Home Care, Senior Living, Rates, and About Us.
Under each of the Header Menu Titles, I would like these drop downs included:
Home Care (drop down pages)- Nurse Aide Care, 24-Hour Home Care, Skilled Nursing, Lifestyle Aide, Hospice at Home, Bathing & Meal Service.
Senior Living (drop down pages) - Long-Term Stay, Short-Term Stay.
Rates (drop down page) - Rates.
About Us (drop down pages) - Our Mission, Ohana Talk, About Dana Marlow.

In the footer, on all pages, you should include the address: 248 Pueo Lane, Suite 310, Honolulu, HI 96817. Phone number: 808-555-0172
The footer should also include buttons for a page called Learn, Caregiver Jobs, and each of the service page links to include: Nurse Aide Care, 24-Hour Home Care, Skilled Nursing, Lifestyle Aide, Hospice at Home, Bathing & Meal Service.
Please don't take the current website and redesign a few aspects. I'm looking for a completely different look and feel.

Target Market(s)

40-80 year olds

Industry/Entity Type

Long Term Healthcare

Coding

Coded - Design and coding required

Requirements
Should not have
• Our existing website as a template. We are looking for a complete redesign. Thank you.

```html
<!DOCTYPE html>
<html lang="en">
<head>
<meta charset="utf-8">
<title>Marlow Health Collective — Homecare &amp; Senior Living</title>
<link href="https://fonts.googleapis.com/css2?family=Montserrat:wght@500;600&family=Roboto:wght@400;500;700&display=swap" rel="stylesheet">
<style>
:root{
  --cream:#f8f4ee;
  --salmon:#e8a084;
  --teal:#6a9288;
  --teal-dark:#5a8479;
  --ink:#222222;
  --muted:#6b6b6b;
  --white:#ffffff;
  --black:#000000;
  --line:#c9c9c9;
}
*{box-sizing:border-box;margin:0;padding:0}
html,body{width:1200px;height:3924px;overflow:hidden}
body{background:var(--cream);font-family:'Roboto',sans-serif;color:var(--ink);position:relative}
a{text-decoration:none}
.abs{position:absolute}
h1,h2,h3{font-family:'Montserrat',sans-serif;font-weight:500}
.btn{position:absolute;display:flex;align-items:center;justify-content:center;font-family:'Roboto',sans-serif;font-weight:700;font-size:13px;letter-spacing:.3px;text-transform:uppercase;border-radius:3px;text-decoration:none}
.btn-salmon{background:var(--salmon);color:var(--white)}
.btn-white{background:var(--white);color:var(--ink)}
.btn-teal{background:var(--teal);color:var(--white)}

/* header */
.site-header{position:absolute;left:0;top:0;width:1200px;height:87px;background:var(--cream)}
.brand{position:absolute;font-family:'Roboto',sans-serif;font-weight:500;font-size:19px;display:flex;align-items:center;gap:6px;color:var(--teal)}
.brand .dot{width:14px;height:14px;border-radius:50%;background:var(--salmon)}
.main-nav{position:absolute;top:31px;left:398px;display:flex;gap:34px;font-size:16px}
.main-nav a{color:var(--ink);position:relative}
.main-nav a.active{color:var(--salmon)}
.main-nav a.active::before{content:"";position:absolute;left:0;right:0;top:-14px;height:3px;background:var(--salmon)}
.call{position:absolute;left:883px;top:22px;display:flex;gap:12px;align-items:center}
.call .icon{width:41px;height:41px;border-radius:4px;background:var(--teal);display:flex;align-items:center;justify-content:center}
.call small{display:block;font-size:15px}
.call strong{display:block;font-size:20px;font-weight:500;margin-top:3px}

/* hero */
.hero{position:absolute;left:0;top:87px;width:1200px;height:590px;overflow:hidden}
.hero-photo{position:absolute;inset:0;background:linear-gradient(100deg,#8a7a68 0%,#b6a592 40%,#6f8fae 62%,#d9cbb8 85%,#a69682 100%)}
.hero h1{position:absolute;left:110px;top:250px;color:var(--white);font-size:46px;line-height:60px;font-weight:600;letter-spacing:.5px}
.hero .btn{left:111px;top:380px;width:157px;height:40px}
.dots{position:absolute;left:110px;top:464px;display:flex;gap:8px}
.dots span{width:11px;height:11px;border-radius:50%;background:rgba(255,255,255,.45)}
.dots span:first-child{background:var(--white)}

/* benefits */
.section-title{position:absolute;left:0;width:1200px;text-align:center;font-size:37px}
.rule{position:absolute;left:565px;width:70px;height:3px;background:var(--teal)}
.card{position:absolute;top:876px;width:560px;height:268px;background:var(--white);border-radius:8px;box-shadow:0 2px 14px rgba(0,0,0,.07)}
.card svg{position:absolute;left:38px;top:44px}
.card h3{position:absolute;left:151px;top:38px;font-size:25px;color:var(--ink)}
.card p{position:absolute;left:151px;top:80px;width:362px;font-size:13.5px;line-height:21.5px;color:var(--muted);text-align:justify}
.card .btn{top:191px;height:42px}

/* about */
.about-photo{position:absolute;left:0;top:1259px;width:1200px;height:512px;background:linear-gradient(90deg,#5c7a3a 0%,#7ea05a 25%,#4d93bd 48%,#e8e2d4 60%,#6aa8c6 80%,#3f7fa6 100%)}
.about-box{position:absolute;left:600px;top:1299px;width:487px;height:433px;background:var(--teal);border-radius:6px}
.about-box .frame{position:absolute;left:20px;top:18px;right:20px;bottom:18px;border:2px solid var(--white);border-radius:6px;text-align:center;color:var(--white)}
.about-box h2{font-size:37px;margin-top:34px}
.about-box .bar{width:60px;height:3px;background:var(--white);margin:14px auto 0}
.about-box p{font-size:15.5px;line-height:25.7px;margin:24px 48px 0}

/* brands */
.panel{position:absolute;color:var(--white)}
.panel h2{position:absolute;font-size:37px}
.panel p{position:absolute;font-size:13.5px;line-height:21.5px}
.panel .btn{height:41px}
.photo-circle{position:absolute;border-radius:50%;border:5px solid var(--white)}

/* schedule */
.schedule-bg{position:absolute;left:0;top:2818px;width:1200px;height:700px;background:linear-gradient(180deg,#f8f4ee,#fbf3ec 60%,#f6efe6)}
.schedule h2{position:absolute;left:0;top:2892px;width:1200px;text-align:center;font-size:42px;line-height:52px}
.field{position:absolute;height:50px;border:1px solid var(--line);background:var(--white);border-radius:3px;font-size:14px;color:var(--muted);padding:17px 17px 0}
.consent{position:absolute;left:0;top:3215px;width:1200px;text-align:center;font-size:14px;color:var(--muted)}

/* footer */
.quote{position:absolute;left:0;top:3515px;width:1200px;text-align:center;color:var(--white);font-size:21px;line-height:31px}
.foot-brand{position:absolute;font-family:'Roboto',sans-serif;font-weight:500;color:var(--white)}
.foot-col{position:absolute;top:3608px;color:var(--white)}
.foot-col h3{font-size:21px;margin-bottom:18px}
.foot-col ul{list-style:none}
.foot-col li{font-size:14px;height:30px;display:flex;align-items:flex-start;gap:20px}
.foot-col li .bullet{width:8px;height:8px;border-radius:50%;background:var(--salmon);margin:4px 6px 0 0}
.foot-col.contact li{gap:18px}
.copyright{position:absolute;left:0;top:3845px;width:1200px;text-align:center;color:var(--white);font-size:15px}
</style>
</head>
<body>

<header class="site-header">
  <div class="brand" style="left:110px;top:30px"><span class="dot"></span>Marlow Homecare</div>
  <div class="brand" style="left:110px;top:55px;font-size:15px;color:var(--teal-dark)">Marlow Senior Living</div>
  <nav class="main-nav">
    <a class="active" href="#">Home Care</a>
    <a href="#">Senior Living</a>
    <a href="#">Rates</a>
    <a href="#">About Us</a>
  </nav>
  <div class="call">
    <div class="icon"><svg width="18" height="18" viewBox="0 0 24 24"><path fill="#fff" d="M6.6 10.8a15 15 0 0 0 6.6 6.6l2.2-2.2a1 1 0 0 1 1-.25 11.4 11.4 0 0 0 3.6.57 1 1 0 0 1 1 1V20a1 1 0 0 1-1 1A17 17 0 0 1 3 4a1 1 0 0 1 1-1h3.5a1 1 0 0 1 1 1c0 1.250.2 2.45.57 3.57a1 1 0 0 1-.25 1z"/></svg></div>
    <div><small>Call Us Today:</small><strong>(808) 555-0172</strong></div>
  </div>
</header>

<section class="hero">
  <div class="hero-photo" role="img" aria-label="Smiling caregiver in blue scrubs embracing an elderly woman at home"></div>
  <h1>Hawaii's Choice<br>Homecare &nbsp;&amp;&nbsp; Senior Living</h1>
  <a class="btn btn-salmon" href="#">Get Started</a>
  <div class="dots"><span></span><span></span><span></span><span></span></div>
  <svg class="abs" style="left:0;top:0" width="1200" height="590" viewBox="0 0 1200 590">
    <path fill="#f8f4ee" d="M0 461 C120 540 240 590 420 587 C640 583 820 520 1000 507 C1090 500 1160 520 1200 548 L1200 590 L0 590 Z"/>
  </svg>
</section>

<h2 class="section-title" style="top:765px">Our Benefits</h2>
<div class="rule" style="top:838px"></div>

<article class="card" style="left:26px">
  <svg width="86" height="86" viewBox="0 0 86 86" fill="none" stroke="#c98770" stroke-width="2.5"><path d="M43 38 C30 28 24 18 32 12 C37 8 42 12 43 15 C44 12 49 8 54 12 C62 18 56 28 43 38Z" stroke="#6a9288"/><path d="M39 22h8M43 18v8" stroke="#6a9288"/><path d="M6 44 L20 64 L30 72 V84 M30 72 L38 62 C40 58 36 56 33 58 L24 66"/><path d="M80 44 L66 64 L56 72 V84 M56 72 L48 62 C46 58 50 56 53 58 L62 66"/></svg>
  <h3>Professional Care In Your Home</h3>
  <p>Marlow Homecare understands that every person's care journey is unique. We tailor our in-home services to meet the diverse nurturing experience of professional quality care and safety within the comfort and convenience of your own home.</p>
  <a class="btn btn-salmon" href="#" style="left:151px;width:266px">Schedule Care Assessment</a>
</article>

<article class="card" style="left:614px">
  <svg width="86" height="120" viewBox="0 0 86 120" fill="none" stroke="#c98770" stroke-width="2.5"><circle cx="43" cy="40" r="36"/><circle cx="43" cy="40" r="25" stroke="#6a9288"/><path d="M43 26l4 9 10 1-7 7 2 10-9-5-9 5 2-10-7-7 10-1z" stroke="#6a9288"/><path d="M26 72 L16 108 L28 100 L34 112 L40 78 M60 72 L70 108 L58 100 L52 112 L46 78"/></svg>
  <h3>Trusted Care In Our Home</h3>
  <p>Marlow Senior Living creates a warm, supportive, and enriching care home environment where seniors can thrive in their golden years. We provide residential care that promotes well-being, connection, and dignity of each individual.</p>
  <a class="btn btn-salmon" href="#" style="left:151px;width:157px">Schedule Tour</a>
</article>

<div class="about-photo" role="img" aria-label="Tropical beach with palm trees and turquoise ocean"></div>
<section class="about-box">
  <div class="frame">
    <h2>About Us</h2>
    <div class="bar"></div>
    <p>At Marlow Health Collective, our mission is to provide compassionate and professional long-term healthcare services that empower individuals to maintain their highest level of independence, health, and well-being, in the comfort of their own homes or ours, either through our licensed home healthcare agency - Marlow Homecare, or in our Adult Residential Care Home - Marlow Senior Living.</p>
  </div>
</section>

<section class="panel" style="left:457px;top:1905px;width:595px;height:328px;background:var(--salmon);border-radius:0 36px 36px 0">
  <h2 style="left:151px;top:44px">Homecare</h2>
  <p style="left:152px;top:108px;width:350px">Marlow Homecare is a leading provider of compassionate and professional homecare services. With a deep commitment to enhancing the quality of life for individuals of all ages, our company is dedicated</p>
  <a class="btn btn-white" href="#" style="left:154px;top:235px;width:157px">Learn More</a>
</section>
<div class="photo-circle" role="img" aria-label="Caregiver and smiling senior woman looking at a photo album" style="left:143px;top:1849px;width:436px;height:436px;background:radial-gradient(circle at 45% 45%,#efe0cc,#c8ab8c 70%,#9c8066)"></div>

<section class="panel" style="left:146px;top:2326px;width:560px;height:327px;background:var(--teal);border-radius:36px 0 0 36px">
  <h2 style="left:84px;top:44px">Senior Living</h2>
  <p style="left:85px;top:108px;width:340px">Choosing a senior living facility is crucial because it directly impacts the quality of life, well-being, and safety of seniors as they age. Marlow Senior Living offers a structured and supportive environment that addresses the unique needs</p>
  <a class="btn btn-white" href="#" style="left:86px;top:234px;width:157px">Learn More</a>
</section>
<div class="photo-circle" role="img" aria-label="Caregiver serving a meal to seniors at a dining table" style="left:624px;top:2269px;width:436px;height:436px;background:radial-gradient(circle at 50% 45%,#e7e3cf,#b3b48d 60%,#7a6450)"></div>

<div class="schedule-bg"></div>
<section class="schedule">
  <h2>Schedule a complimentary<br>Care Consultation</h2>
  <div class="field" style="left:209px;top:3011px;width:249px">Name</div>
  <div class="field" style="left:475px;top:3011px;width:250px">Email</div>
  <div class="field" style="left:742px;top:3011px;width:249px">Phone</div>
  <div class="field" style="left:209px;top:3078px;width:381px">How can we help?</div>
  <div class="field" style="left:609px;top:3078px;width:382px">Questions/comments</div>
  <div class="field" style="left:209px;top:3147px;width:381px">How did you hear about us?</div>
  <div class="field" style="left:609px;top:3147px;width:382px">May email you about this?</div>
  <p class="consent">You agree to receive future emails and understand you may opt-out at any time</p>
  <a class="btn btn-salmon" href="#" style="left:521px;top:3255px;width:157px;height:41px">Submit Now</a>
</section>

<footer>
  <svg class="abs" style="left:0;top:3390px" width="1200" height="534" viewBox="0 0 1200 534">
    <path fill="#000" d="M0 134 C200 100 320 40 560 14 C760 -6 980 10 1200 40 L1200 534 L0 534 Z"/>
  </svg>
  <p class="quote">"Caregiving is a series of small acts of care that alter the<br>course of someone's life."</p>
  <div class="foot-brand" style="left:110px;top:3625px;font-size:22px">Marlow Health Collective</div>
  <div class="foot-brand" style="left:110px;top:3660px;font-size:18px;color:var(--salmon)">Marlow Homecare</div>
  <div class="foot-brand" style="left:110px;top:3692px;font-size:18px;color:var(--teal)">Marlow Senior Living</div>
  <a class="btn btn-salmon" href="#" style="left:136px;top:3748px;width:89px;height:40px">Learn</a>
  <a class="btn btn-teal" href="#" style="left:244px;top:3748px;width:153px;height:40px">Caregiver Jobs</a>

  <div class="foot-col" style="left:475px">
    <h3>Quick Links</h3>
    <ul><li><span class="bullet"></span>Home Page</li><li><span class="bullet"></span>Contact</li><li><span class="bullet"></span>Learn</li><li><span class="bullet"></span>Caregiver Jobs</li><li><span class="bullet"></span>Privacy Policy</li></ul>
  </div>
  <div class="foot-col" style="left:681px">
    <h3>Services</h3>
    <ul><li><span class="bullet"></span>Nurse Aide Care</li><li><span class="bullet"></span>24-Hour Home Care</li><li><span class="bullet"></span>Skilled Nursing</li><li><span class="bullet"></span>Lifestyle Aide</li><li><span class="bullet"></span>Hospice at Home</li><li><span class="bullet"></span>Bathing &amp; Meal Service.</li></ul>
  </div>
  <div class="foot-col contact" style="left:897px">
    <h3>Contact Us</h3>
    <ul>
      <li><svg width="12" height="14" viewBox="0 0 12 16"><path fill="#e8a084" d="M6 0a6 6 0 0 0-6 6c0 4.5 6 10 6 10s6-5.5 6-10a6 6 0 0 0-6-6zm0 8.5A2.5 2.5 0 1 1 6 3.5a2.5 2.5 0 0 1 0 5z"/></svg>248 Pueo Lane, Suite 310</li>
      <li><span style="width:12px"></span>Honolulu, HI 96817</li>
      <li><svg width="12" height="12" viewBox="0 0 24 24"><path fill="#e8a084" d="M6.6 10.8a15 15 0 0 0 6.6 6.6l2.2-2.2a1 1 0 0 1 1-.25 11.4 11.4 0 0 0 3.6.57 1 1 0 0 1 1 1V20a1 1 0 0 1-1 1A17 17 0 0 1 3 4a1 1 0 0 1 1-1h3.5a1 1 0 0 1 1 1c0 1.25.2 2.45.57 3.57a1 1 0 0 1-.25 1z"/></svg>(808) 555-0172</li>
      <li><svg width="12" height="12" viewBox="0 0 24 24" fill="none" stroke="#e8a084" stroke-width="3"><circle cx="12" cy="12" r="10"/><path d="M12 6v6l4 2"/></svg>8:30am - 5:30pm</li>
    </ul>
  </div>
  <p class="copyright">© Copyrights 2024 | All Rights Reserved</p>
</footer>

</body>
</html>
```